Veltrane Group Business Card Design

The CEO is looking for a new trendy look for his business card.
You can stay with current branding or come up with something new/creative. It can be 3D, including Medical Office buildings. You can use our logo in a variety of colors. Please include name, title, company name, company website, email address, cell number

Target Market(s)

Real Estate Development and Construction

Industry/Entity Type

Health care real estate

Contact Information for Business Card

Rohesh Kamdar, CEO M-604.781.2249 E-roheshkamdar@veltrane.com Address:4180 Lindqvist Ave, Tampa, FL 33482 www.veltrane.com

Font styles to use
Other font styles liked:
• Be creative

Requirements
Must have
• Creative, trendy look
Nice to have
• Please go to our website to get a feel- www. veltrane.com
Should not have
• small fonts

```html
<!DOCTYPE html>
<html lang="en">
<head>
<meta charset="utf-8">
<title>Veltrane Group Business Card</title>
<link rel="stylesheet" href="https://fonts.googleapis.com/css2?family=Montserrat:wght@400;700;800&display=swap">
<style>
  :root {
    --backdrop: #3a3a3a;
    --card: #ffffff;
    --brand-red: #b01f29;
    --ink: #222222;
    --card-shadow: rgba(0, 0, 0, 0.35);
  }
  * { box-sizing: border-box; margin: 0; padding: 0; }
  html, body {
    width: 1200px;
    height: 689px;
    overflow: hidden;
    background: var(--backdrop);
    font-family: "Montserrat", sans-serif;
  }
  .stage {
    position: relative;
    width: 1200px;
    height: 689px;
    display: flex;
    align-items: center;
    justify-content: center;
    gap: 40px;
  }
  .card {
    width: 540px;
    height: 310px;
    background: var(--card);
    border-radius: 22px;
    box-shadow: 0 18px 40px var(--card-shadow);
    position: relative;
    overflow: hidden;
  }
  .card-front {
    display: flex;
    align-items: center;
    justify-content: center;
  }
  .wordmark {
    color: var(--brand-red);
    font-weight: 800;
    font-size: 58px;
    letter-spacing: -1px;
    line-height: 1;
  }
  .card-back .identity {
    position: absolute;
    top: 120px;
    right: 318px;
    text-align: right;
  }
  .person-name {
    color: var(--brand-red);
    font-weight: 700;
    font-size: 21px;
    letter-spacing: 0.4px;
    text-transform: uppercase;
    white-space: nowrap;
  }
  .person-title {
    color: var(--ink);
    font-weight: 400;
    font-size: 17px;
    margin-top: 2px;
  }
  .divider {
    position: absolute;
    left: 238px;
    top: 88px;
    width: 2px;
    height: 104px;
    background: var(--brand-red);
  }
  .contact-list {
    position: absolute;
    left: 256px;
    top: 92px;
    list-style: none;
  }
  .contact-list li {
    display: flex;
    align-items: center;
    gap: 9px;
    color: var(--ink);
    font-size: 15px;
    line-height: 32px;
    white-space: nowrap;
  }
  .contact-list svg { width: 14px; height: 14px; flex: none; }
  .address {
    position: absolute;
    right: 40px;
    bottom: 40px;
    color: var(--ink);
    font-size: 17px;
    white-space: nowrap;
  }
</style>
</head>
<body>
<main class="stage">
  <section class="card card-front" aria-label="Card front">
    <span class="wordmark">Veltrane Group</span>
  </section>

  <section class="card card-back" aria-label="Card back">
    <div class="identity">
      <p class="person-name">Rohesh Kamdar</p>
      <p class="person-title">CEO</p>
    </div>
    <span class="divider"></span>
    <ul class="contact-list">
      <li>
        <svg viewBox="0 0 14 14" aria-hidden="true"><rect x="3.5" y="1" width="7" height="12" rx="1.2" fill="none" stroke="var(--brand-red)" stroke-width="1.5"/><circle cx="7" cy="10.8" r="0.8" fill="var(--brand-red)"/></svg>
        604.781.2249
      </li>
      <li>
        <svg viewBox="0 0 14 14" aria-hidden="true"><rect x="1" y="3" width="12" height="8.5" fill="var(--brand-red)"/><path d="M1 3 L7 8 L13 3" fill="none" stroke="#fff" stroke-width="1.2"/></svg>
        roheshkamdar@veltrane.com
      </li>
      <li>
        <svg viewBox="0 0 14 14" aria-hidden="true"><circle cx="7" cy="7" r="6" fill="var(--brand-red)"/><path d="M1 7 H13 M7 1 C4 4 4 10 7 13 M7 1 C10 4 10 10 7 13" fill="none" stroke="#fff" stroke-width="0.9"/></svg>
        www.veltrane.com
      </li>
    </ul>
    <p class="address">4180 Lindqvist Ave, Tampa, FL 33482</p>
  </section>
</main>
</body>
</html>
```